Letterhead Design for Law Firm

**Edit: I have added the photo of a bottom that I like.

------
We are looking for a re-design of our new letterhead. The letterhead is for a law firm and will be used for digital and traditionally printed correspondence.

Here are some suggestions:

- Please use colours are #8ec900 and simple black.
- Please do not use any type of "waves" at the bottom of the page. This is not in style at all.
- Please stay modern yet conservative.
- Please use font Segoe UI Light or similar if you can
- Avoid clipart or illustrations.
- Utilize ample white space in the layout so the design looks clean and information is easy to read at a glance. Don't overcrowd the letterhead.
- Make sure the letterhead design is consistent with our brand identity (see corvelith.ca)
-Please, no black headers or footers.

I am attaching my current letterhead and signature for your convenience.

Remember, the letterhead is an extension of our professional identity. We are a successful firm and trial lawyers who correspond with insurers, judges, lawyers, courts, clients, etc. Make it new, modern, attractive, yet powerful and conservative.

It needs to be easily printable. I would like the bleed removed in print so the black bar the bottom crosses the page (but the text is not near the edges)
Updates

Low design quality

Target Market(s)

Clients, Government Offices, Judiciary, Lawyers, Insurance Companies, Colleagues.

Industry/Entity Type

Law

Other font styles liked:
• Segoe UI LIght, Calibri Light,

Colors
00AB8E
00BBA5
67D7C9
C6EFE9
E9F9F6

Requirements
Must have
• Everything that is on the letterhead now.
Nice to have
• Cutting Edge design, yet conservative.
Should not have
• law firm cliche design, images,

```html
<!DOCTYPE html>
<html lang="en">
<head>
<meta charset="utf-8">
<title>Corvelith Letterhead</title>
<link rel="stylesheet" href="https://fonts.googleapis.com/css2?family=Open+Sans:wght@300;400;600;700&display=swap">
<style>
  :root {
    --brand-green: #8ec900;
    --ink: #111111;
    --paper: #ffffff;
    --backdrop: #d4d4d4;
  }
  * { margin: 0; padding: 0; box-sizing: border-box; }
  html, body {
    width: 1200px; height: 686px; overflow: hidden;
    background: var(--backdrop);
    font-family: "Open Sans", "Segoe UI", sans-serif;
    color: var(--ink);
  }
  .letterhead {
    position: absolute; left: 345px; top: 13px;
    width: 510px; height: 660px;
    background: var(--paper);
    overflow: hidden;
    box-shadow: 0 4px 18px rgba(0,0,0,0.18);
  }
  .letterhead > * { position: absolute; }
  .footer-band { left: 0; top: 0; width: 510px; height: 660px; }
  .firm-name {
    left: 30px; top: 20px;
    font-size: 30px; font-weight: 400; letter-spacing: 1px;
    color: var(--ink); line-height: 1;
  }
  .sidebar {
    left: 340px; top: 20px;
    border-left: 1.5px solid var(--brand-green);
    padding-left: 9px;
    font-size: 8px; line-height: 10.6px;
  }
  .sidebar .web { color: var(--brand-green); }
  .sidebar .practice { margin-top: 8px; }
  .body-block { left: 30px; top: 74px; font-size: 8.6px; line-height: 11px; }
  .body-block p { margin-bottom: 8px; }
  .strong { font-weight: 700; }
  .address { margin-left: 18px; }
  .re-row { display: flex; }
  .re-label { width: 82px; }
  .re-subject { font-weight: 700; }
  .divider {
    left: 30px; top: 298px; width: 450px; height: 1.5px;
    background: var(--brand-green);
  }
  .closing { left: 30px; top: 436px; font-size: 8.6px; line-height: 11px; }
  .closing .sign-area {
    width: 120px; height: 36px; margin: 3px 0 3px 10px;
    background: linear-gradient(90deg, #e9e9e9, #f5f5f5);
  }
  .closing .muted { font-weight: 300; }
</style>
</head>
<body>
  <main class="letterhead">
    <svg class="footer-band" viewBox="0 0 510 660" aria-hidden="true">
      <path d="M0,598 C130,636 300,654 470,660 L0,660 Z" fill="var(--brand-green)"/>
      <path d="M0,580 C130,620 240,642 310,653 C230,640 120,618 0,590 Z" fill="var(--ink)"/>
    </svg>

    <div class="firm-name">CORVELITH</div>

    <aside class="sidebar">
      <div class="web">www.CORVELITH.ca</div>
      <div>48 Carrow Street W, Suite 1210</div>
      <div>Hamilton, ON L8P 0A0</div>
      <div>T: 905-555-0142</div>
      <div>F: 905-555-0177</div>
      <div>File Clerk: Nadia Fairhurst</div>
      <div>Email: nadia@corvelith.ca</div>
      <div class="practice">
        <div>Practice Restricted</div>
        <div>Serious Personal Injury</div>
        <div>Wrongful Death Litigation</div>
        <div>Long-Term Disability Litigation</div>
        <div>Wrongful Dismissal Litigation</div>
        <div>Employee Terminations</div>
      </div>
    </aside>

    <section class="body-block">
      <p class="strong">Without Prejudice</p>
      <p>March 13, 2024</p>
      <p class="strong">By Email</p>
      <p class="address">
        Meridale Insurance Company<br>
        Claims Litigation Department<br>
        240 Birchline Road South<br>
        P.O. Box 1500<br>
        Waterloo, ON&nbsp;&nbsp;N2J 0B0
      </p>
      <p>Attention:&nbsp; Mr. Dalton Reeve</p>
      <p>Mr. Reeve:</p>
      <div class="re-row">
        <span class="re-label">Re:</span>
        <span class="re-subject">
          Halvorsen v. Petrak et al.<br>
          DOL: September 12, 2019<br>
          Pre-Mediation Settlement Proposal – March 13th, 2024
        </span>
      </div>
    </section>

    <div class="divider"></div>

    <section class="closing">
      <div>Yours very truly,</div>
      <div>CORVELITH PERSONAL INJURY LAWYERS</div>
      <div class="sign-area" role="img" aria-label="Handwritten signature of Owen T. Corvel"></div>
      <div class="muted">Owen T. Corvel</div>
      <div>Corvel Law Professional Corporation</div>
      <div class="muted">/nf</div>
      <div class="muted">Encl.</div>
    </section>
  </main>
</body>
</html>
```